Clear Plastic Card Design

I am looking to have a business card designed from my logo icon. I am looking to match the style of a different business card I have attached in the files.
Looking for a card that is plastic, with layers of transparency in the shape of my logo icon (also attached in the files) - not a circle like the other card. The winning design will incorporate the red icon logo on the front and back and include the charity's name, "Light for the Weary Souls" in the same or similar font, as well as an email and phone number. For now, use the email: email@lightfortheweary-mail.org and the phone number 555-382-7194.
We like how the sample business card has transparency, partial and full opacity layers and a matching color scheme. Files will need to be in vector so that our business card printing company can work with it.
UPDATE:
We've some excellent designs in, thank you everyone! I got an early review from the owner, and he requested a minor redirect to find his perfect design. He wants the design to stand out by NOT being a rectangle. Try instead a circle, square, or best yet - something that falls in the outline of the logo icon, either fully or partially. Thank you, everyone!
Light for the Weary Souls text should be incorporated as well as a phone and email.

```html
<!DOCTYPE html>
<html lang="en">
<head>
<meta charset="utf-8">
<title>Light for the Weary Souls – Business Card</title>
<link rel="stylesheet" href="https://fonts.googleapis.com/css2?family=Hind:wght@700&family=Open+Sans:ital,wght@0,600;1,700&display=swap">
<style>
  :root {
    --backdrop: #ebe7e5;
    --card-red: #c80a12;
    --card-orange: #ee6a10;
    --card-mid: #e2411a;
    --text-light: #ffffff;
    --disc-fill: rgba(255, 255, 255, 0.82);
    --disc-edge: rgba(240, 120, 100, 0.55);
    --mark-red: #d3261a;
  }
  html, body {
    margin: 0;
    padding: 0;
    width: 1200px;
    height: 900px;
    overflow: hidden;
    background: var(--backdrop);
  }
  .canvas {
    position: relative;
    width: 1200px;
    height: 900px;
  }
  .card {
    position: absolute;
    left: 353px;
    top: 166px;
    width: 701px;
    height: 567px;
    background:
      radial-gradient(ellipse 48% 46% at 58% 50%, var(--card-orange) 0%, var(--card-mid) 55%, rgba(226, 65, 26, 0) 100%),
      linear-gradient(90deg, var(--card-red) 0%, #d8261a 50%, var(--card-red) 100%);
    box-shadow: 0 14px 40px rgba(0, 0, 0, 0.12);
  }
  .card-title {
    position: absolute;
    left: 120px;
    right: 0;
    top: 40px;
    margin: 0;
    text-align: center;
    font-family: "Hind", sans-serif;
    font-weight: 700;
    font-size: 52px;
    line-height: 63px;
    letter-spacing: 0.5px;
    color: var(--text-light);
    text-transform: uppercase;
  }
  .card-divider {
    position: absolute;
    left: 390px;
    top: 266px;
    width: 59px;
    height: 1px;
    background: var(--text-light);
    opacity: 0.85;
  }
  .card-phone {
    position: absolute;
    left: 120px;
    right: 0;
    top: 418px;
    text-align: center;
    font-family: "Open Sans", sans-serif;
    font-weight: 600;
    font-size: 40px;
    color: var(--text-light);
  }
  .card-email {
    position: absolute;
    left: 120px;
    right: 0;
    top: 480px;
    text-align: center;
    font-family: "Open Sans", sans-serif;
    font-style: italic;
    font-weight: 700;
    font-size: 25px;
    color: var(--text-light);
  }
  .brand-disc {
    position: absolute;
    left: 146px;
    top: 243px;
    width: 412px;
    height: 412px;
    border-radius: 50%;
    background: var(--disc-fill);
    box-shadow: inset -4px 0 0 var(--disc-edge), 0 6px 22px rgba(0, 0, 0, 0.08);
    display: flex;
    align-items: center;
    justify-content: center;
  }
  .brand-name {
    margin: 0;
    width: 280px;
    text-align: center;
    font-family: "Hind", sans-serif;
    font-weight: 700;
    font-size: 46px;
    line-height: 50px;
    color: var(--mark-red);
    text-transform: uppercase;
  }
</style>
</head>
<body>
  <main class="canvas">
    <section class="card">
      <h1 class="card-title">Light for the<br>Weary Souls</h1>
      <div class="card-divider"></div>
      <div class="card-phone">555-382-7194</div>
      <div class="card-email">email@lightfortheweary-mail.org</div>
    </section>
    <div class="brand-disc">
      <p class="brand-name">Light for the Weary Souls</p>
    </div>
  </main>
</body>
</html>
```